Web design

We need the design for the logo and website for a women fashion website. No coding required. The colors used should be neutral (maybe with a light touch of color), the style should be modern, slightly luxurious, not too crowded. The target market is young professionals who love trendy clothes.
Updates

Need extra days to review

Target Market(s)

Young professionals

Industry/Entity Type

Apparel

Number of Pages Required

5+ page

Font styles to use
Sans Serif
Other font styles liked:
• Montserrat, Engravers Gothic, Benton Sans, gotham-book

Colors

Designer to choose colors to be used in the design.

```html
<!DOCTYPE html>
<html lang="en">
<head>
<meta charset="utf-8">
<title>LUMA Women's Fashion</title>
<link href="https://fonts.googleapis.com/css2?family=Montserrat:wght@400;500;600;700&display=swap" rel="stylesheet">
<style>
:root{
  --ink:#1b1b1b;
  --muted:#6b6b6b;
  --white:#ffffff;
  --accent:#e0457b;
  --tan:#d8c3a8;
  --blush:#f8e4e7;
  --sand:#f3efec;
  --line:#d9d9d9;
  --footer:#000000;
}
*{box-sizing:border-box;margin:0;padding:0}
html,body{width:1200px;height:4020px;overflow:hidden;background:var(--white);font-family:'Montserrat',sans-serif;color:var(--ink)}
.page{position:relative;width:1200px;height:4020px}

/* header */
.site-header{position:relative;height:172px;display:flex;align-items:center;justify-content:space-between;padding:0 72px}
.social{display:flex;gap:12px;align-items:center}
.social span{width:15px;height:15px;border-radius:50%;border:2px solid var(--ink);display:block}
.brand{position:absolute;left:50%;top:36px;transform:translateX(-50%);display:flex;align-items:center;gap:14px;border:1px solid var(--line);padding:12px 26px}
.brand-mark{width:60px;height:60px;background:var(--ink)}
.brand-text{font-weight:600;font-size:50px;letter-spacing:2px;line-height:1}
.brand-sub{font-size:13px;letter-spacing:4px;font-weight:600;margin-top:6px}
.utility{display:flex;gap:18px;align-items:center;font-size:13px;font-weight:600}
.utility svg{width:20px;height:20px}

/* hero */
.hero{position:relative;height:668px;background:
  radial-gradient(ellipse 260px 330px at 38% 58%,#e9c9ad 0%,rgba(233,201,173,0) 100%),
  radial-gradient(ellipse 240px 320px at 62% 60%,#b5684a 0%,rgba(181,104,74,0) 100%),
  linear-gradient(115deg,#aebccb 0%,#d9c6ae 35%,#c89676 60%,#6f7d5a 82%,#cfd9e0 100%)}
.nav{position:absolute;top:22px;left:0;right:0;display:flex;justify-content:center;gap:72px;font-size:14px;font-weight:700;letter-spacing:1px}
.hero-copy{position:absolute;top:290px;width:100%;text-align:center;color:var(--white)}
.hero-copy h1{font-size:48px;font-weight:700;letter-spacing:1px}
.hero-copy p{font-size:17px;margin-top:6px}
.btn-shop{display:inline-block;margin-top:26px;background:var(--tan);color:var(--ink);font-size:15px;padding:16px 26px}
.hero-arrow{position:absolute;top:340px;width:20px;height:30px}

/* perks */
.perks{display:flex;gap:32px;padding:28px 72px 0}
.perk{flex:1;height:146px;background:var(--blush);text-align:center;padding-top:18px}
.perk svg{width:62px;height:52px}
.perk h3{font-size:13px;font-weight:700;color:var(--accent);margin-top:6px;line-height:1.35}
.perk p{font-size:12px;margin-top:4px}

/* collections */
.section-title{font-size:40px;font-weight:500;text-align:center;letter-spacing:1px}
.collections{padding-top:56px}
.grid-3,.grid-2{display:flex;gap:32px;padding:0 72px}
.grid-3{margin-top:44px}
.grid-2{margin-top:24px}
.tile{flex:1}
.tile .photo{height:320px}
.tile h4{text-align:center;font-size:17px;font-weight:600;margin-top:22px}

/* products */
.featured{margin-top:72px;height:780px;background:var(--sand);padding-top:58px;position:relative}
.products{display:flex;justify-content:center;gap:28px;margin-top:40px}
.product{width:244px;text-align:center}
.product .photo{height:350px}
.product h5{font-size:15px;font-weight:700;margin-top:26px}
.product .desc{font-size:13px;color:var(--muted);margin-top:6px}
.product .price{font-size:14px;font-weight:700;color:var(--accent);margin-top:8px}
.slide-arrow{position:absolute;top:380px;width:22px;height:14px}
.pager{margin-top:56px;font-size:15px;font-weight:600;display:flex;justify-content:center;gap:22px;align-items:center}

/* gallery */
.tag-title{font-size:28px;font-weight:500;text-align:center;margin-top:30px}
.gallery{display:grid;grid-template-columns:300px 300px 300px 300px;grid-template-rows:240px 240px;margin-top:32px}
.gallery .tall{grid-row:span 2}

/* newsletter */
.newsletter{text-align:center;padding-top:56px}
.newsletter h2{font-size:40px;font-weight:500}
.newsletter p{font-size:15px;color:var(--muted);margin-top:14px}
.signup{display:flex;justify-content:center;gap:6px;margin-top:26px}
.signup .field{width:520px;height:62px;background:var(--sand);font-size:12px;font-weight:600;text-align:left;padding:24px 16px}
.signup .submit{width:164px;height:62px;background:var(--tan);font-size:13px;font-weight:700;padding-top:24px}

/* footer */
.site-footer{position:absolute;top:3660px;left:0;width:1200px;height:360px;background:var(--footer);color:var(--white);padding:42px 72px 0}
.cols{display:flex}
.col h6{font-size:18px;font-weight:600;margin-bottom:16px}
.col li{list-style:none;font-size:13px;margin-bottom:12px}
.col-help{width:272px}
.col-shop{width:448px}
.footer-social{display:flex;gap:18px}
.footer-social span{width:22px;height:22px;border-radius:50%;border:2px solid var(--white);display:block}
.legal{position:absolute;left:72px;right:72px;bottom:30px;display:flex;justify-content:space-between;align-items:center;font-size:11px}
.cards{display:flex;gap:8px}
.cards span{width:46px;height:28px;border-radius:3px;display:block}
</style>
</head>
<body>
<div class="page">

<header class="site-header">
  <div class="social"><span></span><span></span><span></span><span></span></div>
  <div class="brand">
    <div class="brand-mark"></div>
    <div><div class="brand-text">LUMA</div><div class="brand-sub">WOMEN'S FASHION</div></div>
  </div>
  <div class="utility">
    <svg viewBox="0 0 20 20" fill="none" stroke="#1b1b1b" stroke-width="2"><circle cx="8" cy="8" r="6"/><line x1="13" y1="13" x2="18" y2="18"/></svg>
    <svg viewBox="0 0 20 20" fill="#1b1b1b"><circle cx="10" cy="6" r="4"/><path d="M2 19c0-5 4-7 8-7s8 2 8 7z"/></svg>
    <svg viewBox="0 0 20 20" fill="#1b1b1b"><path d="M10 18 2 10a4.5 4.5 0 0 1 8-5 4.5 4.5 0 0 1 8 5z"/></svg>
    <svg viewBox="0 0 20 20" fill="none" stroke="#1b1b1b" stroke-width="2"><path d="M2 3h3l2 10h10l2-7H6"/><circle cx="8" cy="17" r="1.5"/><circle cx="16" cy="17" r="1.5"/></svg>
    <span>EN ▾</span>
  </div>
</header>

<section class="hero" role="img" aria-label="Two smiling young women in sunglasses under palm trees">
  <nav class="nav"><span>HOME</span><span>LATEST ARRIVALS</span><span>CLOTHES</span><span>CONTACT US</span></nav>
  <svg class="hero-arrow" style="left:94px" viewBox="0 0 20 30"><path d="M15 3 4 15l11 12" fill="none" stroke="#fff" stroke-width="3"/></svg>
  <svg class="hero-arrow" style="right:94px" viewBox="0 0 20 30"><path d="M5 3l11 12L5 27" fill="none" stroke="#fff" stroke-width="3"/></svg>
  <div class="hero-copy">
    <h1>WELCOME TO LUMA</h1>
    <p>Sed ut perspiciatis unde omnis iste natus error sit voluptatem accusantium</p>
    <span class="btn-shop">Shop Now</span>
  </div>
</section>

<section class="perks">
  <div class="perk">
    <svg viewBox="0 0 56 48" fill="none" stroke="#1b1b1b" stroke-width="2.5"><rect x="4" y="10" width="30" height="24"/><path d="M34 18h10l8 8v8H34"/><circle cx="14" cy="38" r="4"/><circle cx="42" cy="38" r="4"/></svg>
    <h3>SHIPPING WORLDWIDE</h3><p>Click for more info</p>
  </div>
  <div class="perk">
    <svg viewBox="0 0 56 48" fill="none" stroke="#1b1b1b" stroke-width="2.5"><rect x="16" y="18" width="24" height="22"/><path d="M22 18v-6a6 6 0 0 1 12 0v6"/><line x1="6" y1="44" x2="50" y2="44"/></svg>
    <h3>FREE SHIPPING ON ORDERS<br>GREATER THAN 50</h3><p>Click for more info</p>
  </div>
  <div class="perk">
    <svg viewBox="0 0 56 48" fill="none" stroke="#1b1b1b" stroke-width="2.5"><rect x="10" y="8" width="36" height="34"/><line x1="10" y1="18" x2="46" y2="18"/><path d="M20 30l5 5 10-10"/></svg>
    <h3>30 DAYS RETURN POLICY</h3><p>Click for more info</p>
  </div>
</section>

<section class="collections">
  <h2 class="section-title">Latest Collections</h2>
  <div class="grid-3">
    <div class="tile"><div class="photo" role="img" aria-label="Woman in a beige trench dress" style="background:radial-gradient(ellipse 70px 150px at 50% 60%,#a97a55,rgba(169,122,85,0)),linear-gradient(180deg,#efe4d8,#d9c3ad)"></div><h4>Vivamus Egestas</h4></div>
    <div class="tile"><div class="photo" role="img" aria-label="Woman in a grey checked coat" style="background:radial-gradient(ellipse 90px 160px at 52% 62%,#5f5f63,rgba(95,95,99,0)),linear-gradient(160deg,#d6d6d6,#9b9b9b)"></div><h4>Vivamus Egestas</h4></div>
    <div class="tile"><div class="photo" role="img" aria-label="Woman in a white blouse outdoors" style="background:radial-gradient(ellipse 80px 130px at 50% 62%,#f7f7f5,rgba(247,247,245,0)),linear-gradient(160deg,#f5e7b8,#a89a6c 50%,#4f5a3c)"></div><h4>Vivamus Egestas</h4></div>
  </div>
  <div class="grid-2">
    <div class="tile"><div class="photo" role="img" aria-label="Woman in a pink outfit against a pink wall" style="background:radial-gradient(ellipse 110px 150px at 40% 60%,#f7c7c9,rgba(247,199,201,0)),linear-gradient(160deg,#f09aab,#e4768b)"></div><h4>Vivamus Egestas</h4></div>
    <div class="tile"><div class="photo" role="img" aria-label="Woman in a hat and brown jacket in tall grass" style="background:radial-gradient(ellipse 90px 150px at 50% 60%,#7a4e2e,rgba(122,78,46,0)),linear-gradient(180deg,#5f86ad,#a7b6c4 40%,#b99a72 65%,#7a5a3a)"></div><h4>Vivamus Egestas</h4></div>
  </div>
</section>

<section class="featured">
  <h2 class="section-title">Featured Products</h2>
  <svg class="slide-arrow" style="left:38px" viewBox="0 0 22 14"><path d="M22 7H4M9 1 2 7l7 6" fill="none" stroke="#1b1b1b" stroke-width="2.5"/></svg>
  <svg class="slide-arrow" style="right:38px" viewBox="0 0 22 14"><path d="M0 7h18M13 1l7 6-7 6" fill="none" stroke="#1b1b1b" stroke-width="2.5"/></svg>
  <div class="products">
    <div class="product"><div class="photo" role="img" aria-label="Model in a light blue top and jeans" style="background:radial-gradient(ellipse 40px 80px at 50% 32%,#bcd9ee,rgba(188,217,238,0)),radial-gradient(ellipse 28px 95px at 50% 68%,#5f82ad,rgba(95,130,173,0)),#fff"></div><h5>PRODUCT NAME</h5><p class="desc">Aliquam molestie</p><p class="price">$99.00</p></div>
    <div class="product"><div class="photo" role="img" aria-label="Model in a floral maxi dress" style="background:radial-gradient(ellipse 38px 140px at 50% 55%,#6cbf94,rgba(108,191,148,0)),radial-gradient(ellipse 30px 60px at 50% 60%,#e58fa8,rgba(229,143,168,0)),#fff"></div><h5>PRODUCT NAME</h5><p class="desc">Aliquam molestie</p><p class="price">$99.00</p></div>
    <div class="product"><div class="photo" role="img" aria-label="Model in a short printed dress" style="background:radial-gradient(ellipse 40px 90px at 50% 45%,#b7c8ad,rgba(183,200,173,0)),radial-gradient(ellipse 18px 70px at 50% 78%,#e6cdb7,rgba(230,205,183,0)),#fff"></div><h5>PRODUCT NAME</h5><p class="desc">Aliquam molestie</p><p class="price">$99.00</p></div>
    <div class="product"><div class="photo" role="img" aria-label="Model in a green patterned dress" style="background:radial-gradient(ellipse 40px 90px at 50% 45%,#6fbf86,rgba(111,191,134,0)),radial-gradient(ellipse 24px 40px at 50% 50%,#e9a0b0,rgba(233,160,176,0)),radial-gradient(ellipse 18px 70px at 50% 78%,#e6cdb7,rgba(230,205,183,0)),#fff"></div><h5>PRODUCT NAME</h5><p class="desc">Aliquam molestie</p><p class="price">$99.00</p></div>
  </div>
  <div class="pager"><span>←</span><span>1 / 2 / 3</span><span>→</span></div>
</section>

<h2 class="tag-title"># Luma</h2>
<section class="gallery">
  <div class="tall" role="img" aria-label="Woman in a black off-shoulder dress" style="background:radial-gradient(ellipse 100px 200px at 50% 65%,#151515,rgba(21,21,21,0)),linear-gradient(180deg,#efeae4,#cfc6bc)"></div>
  <div role="img" aria-label="Woman in a dark dress on rocks" style="background:radial-gradient(ellipse 60px 100px at 55% 55%,#3e3430,rgba(62,52,48,0)),linear-gradient(160deg,#9db0a0,#b9b1a6 50%,#8b7d70)"></div>
  <div class="tall" role="img" aria-label="Woman in a plaid outfit and white sneakers" style="background:radial-gradient(ellipse 110px 150px at 45% 50%,#7d4a36,rgba(125,74,54,0)),linear-gradient(180deg,#d9d6d2,#c7c3bd 60%,#eeeeee)"></div>
  <div role="img" aria-label="Woman in a white top among palms" style="background:radial-gradient(ellipse 70px 90px at 50% 60%,#f4f4f4,rgba(244,244,244,0)),linear-gradient(160deg,#6f9b58,#b9cbb1 60%,#dde3e8)"></div>
  <div role="img" aria-label="Woman in a dark coat on a terrace" style="background:radial-gradient(ellipse 60px 110px at 45% 55%,#2f2f33,rgba(47,47,51,0)),linear-gradient(160deg,#cbd3dc,#8d949c)"></div>
  <div role="img" aria-label="Woman in a flowing yellow gown" style="background:radial-gradient(ellipse 120px 90px at 50% 70%,#f2a81e,rgba(242,168,30,0)),linear-gradient(160deg,#b8a58c,#d6b48a)"></div>
</section>

<section class="newsletter">
  <h2>Subscribe to Newsletter</h2>
  <p>Neque porro quisquam est qui dolorem ipsum quia dolor sit amet.</p>
  <div class="signup"><div class="field">EMAIL ADDRESS</div><div class="submit">SUBSCRIBE</div></div>
</section>

<footer class="site-footer">
  <div class="cols">
    <div class="col col-help"><h6>Help</h6><ul><li>Email address</li><li>Returns/exchanges</li><li>Delivery Information</li><li>FAQ</li></ul></div>
    <div class="col col-shop"><h6>Shop</h6><ul><li>Sed ut perspiciatis</li><li>Unde omnis iste</li><li>Natus error sit voluptatem</li><li>Accusantium</li></ul></div>
    <div class="col"><h6>Follow Us</h6><div class="footer-social"><span></span><span></span><span></span><span></span></div></div>
  </div>
  <div class="legal">
    <span>Copyright © 2021, Company Name. All Rights Reserved. · Terms &amp; Conditions · Privacy Policy</span>
    <div class="cards">
      <span style="background:#2b4ea2"></span>
      <span style="background:#e7e7e7"></span>
      <span style="background:#f2a23a"></span>
      <span style="background:#2d8fd5"></span>
      <span style="background:#e7e7e7"></span>
      <span style="background:#6a7bd1"></span>
    </div>
  </div>
</footer>

</div>
</body>
</html>
```